Local Flower Farm Needs Business Card Design

I need business cards designed for a flower farm based in Eudora, Kansas.
Business Info:
We are a local cut flower farm located in Eudora, Kansas, founded by Corinne Haldwick. What started as a passion for agriculture and search for more joy in daily life has blossomed into a small business dedicated to providing the community with beautiful, fresh, and sustainable flowers. We specialize in local, seasonal blooms, ensuring that every petal reflects the care and dedication we pour into our craft. Our mission is to deliver the highest quality flowers directly to our customers through local farmers markets and to florists who share our commitment to sustainability. Join us in celebrating the beauty of nature, one bloom at a time!
Contact Details:
Corinne Haldwick
Owner
Phone 913-555-0147
Facebook: Rosalind Thorpe Gardens
Instagram: @RosalindThorpeGardens
Website: RosalindThorpeGardens.example
Target Market(s)
Wholesale to Florists and Direct to Consumer via Farmers Market
Industry/Entity Type
Florist, Farm
Contact Information for Business Card
Name, Contact Info, Logo
Look and feel
Each slider illustrates characteristics of the customer's brand and the style your logo design should communicate.

```html
<!DOCTYPE html>
<html lang="en">
<head>
<meta charset="utf-8">
<title>Rosalind Thorpe Gardens – Business Card</title>
<link href="https://fonts.googleapis.com/css2?family=Tinos:wght@400;700&display=swap" rel="stylesheet">
<style>
  :root {
    --backdrop: #dfe4e6;
    --card: #0a252d;
    --ink-light: #ffffff;
    --emboss: #1d4a4f;
    --emboss-line: #16393f;
  }
  * { margin: 0; padding: 0; box-sizing: border-box; }
  html, body {
    width: 1200px; height: 960px; overflow: hidden;
    background: var(--backdrop);
    font-family: "Tinos", "Times New Roman", serif;
  }
  .card {
    position: absolute;
    left: 248px;
    width: 704px;
    height: 402px;
    background: var(--card);
    color: var(--ink-light);
  }
  .card-front { top: 58px; }
  .card-back { top: 500px; }

  .brand-seal {
    position: absolute;
    border-radius: 50%;
    display: flex; align-items: center; justify-content: center;
    text-align: center;
  }
  .card-front .brand-seal {
    left: 217px; top: 66px; width: 272px; height: 272px;
    border: 1px solid var(--ink-light);
  }
  .brand-name {
    font-weight: 400;
    letter-spacing: 3px;
    text-transform: uppercase;
    line-height: 1.35;
  }
  .card-front .brand-name { font-size: 24px; color: var(--ink-light); }

  .card-back .brand-seal {
    left: 34px; top: 51px; width: 294px; height: 294px;
    border: 2px solid var(--emboss-line);
  }
  .card-back .brand-name { font-size: 26px; color: var(--emboss); }

  .holder {
    position: absolute;
    right: 30px; top: 50px;
    text-align: right;
  }
  .holder-name { font-size: 33px; font-weight: 700; letter-spacing: 1px; line-height: 1.1; }
  .holder-role { font-size: 17px; font-weight: 400; letter-spacing: 0.5px; margin-top: 2px; }
  .accent-bar {
    position: absolute;
    right: 0; top: 52px;
    width: 18px; height: 50px;
    background: var(--ink-light);
  }

  .contact-list {
    position: absolute;
    right: 28px; top: 276px;
    list-style: none;
    text-align: right;
  }
  .contact-list li {
    display: flex; align-items: center; justify-content: flex-end;
    gap: 12px;
    font-size: 17.5px; letter-spacing: 0.4px;
    height: 24px;
  }
  .contact-icon { width: 17px; height: 17px; flex: none; }
</style>
</head>
<body>
  <section class="card card-front" aria-label="Card front">
    <div class="brand-seal">
      <p class="brand-name">Rosalind Thorpe<br>Gardens</p>
    </div>
  </section>

  <section class="card card-back" aria-label="Card back">
    <div class="brand-seal">
      <p class="brand-name">Rosalind Thorpe<br>Gardens</p>
    </div>

    <div class="holder">
      <h1 class="holder-name">Corinne Haldwick</h1>
      <p class="holder-role">Owner</p>
    </div>
    <div class="accent-bar"></div>

    <ul class="contact-list">
      <li>913-555-0147
        <svg class="contact-icon" viewBox="0 0 24 24" aria-label="Phone">
          <path d="M6.6 10.8a15 15 0 0 0 6.6 6.6l2.2-2.2c.3-.3.7-.4 1-.2 1.1.4 2.3.6 3.6.6.6 0 1 .4 1 1V20c0 .6-.4 1-1 1A17 17 0 0 1 3 4c0-.6.4-1 1-1h3.5c.6 0 1 .4 1 1 0 1.3.2 2.5.6 3.6.1.3 0 .7-.2 1z" fill="#fff"/>
        </svg>
      </li>
      <li>Rosalind Thorpe Gardens
        <svg class="contact-icon" viewBox="0 0 24 24" aria-label="Social page"><circle cx="12" cy="12" r="11" fill="#fff"/></svg>
      </li>
      <li>@RosalindThorpeGardens
        <svg class="contact-icon" viewBox="0 0 24 24" aria-label="Social handle"><circle cx="12" cy="12" r="11" fill="#fff"/></svg>
      </li>
      <li>RosalindThorpeGardens.example
        <svg class="contact-icon" viewBox="0 0 24 24" aria-label="Website">
          <circle cx="12" cy="12" r="10" fill="none" stroke="#fff" stroke-width="2"/>
          <ellipse cx="12" cy="12" rx="4.5" ry="10" fill="none" stroke="#fff" stroke-width="1.6"/>
          <line x1="2" y1="12" x2="22" y2="12" stroke="#fff" stroke-width="1.6"/>
        </svg>
      </li>
    </ul>
  </section>
</body>
</html>
```